Prospekt für Exklusive Busreisen zu besonderen Zielen!
Zielgruppe
Unser Prospekt soll, ansprechend und Jung sein aber nicht abstoßend dem älteren Publikum gegenüber. Modern und Spritzig. Es soll Ruhe ausstrahlen aber auch für Familien mit Kindern ein Erlebnis werden.
einmalig... besonders... sorgenfrei...Urlaub von Anfang an ohne Kompromisse…
Ich bin gespannt auf die tollen Entwürfe.
Anbei unser Logo und Busbilder. Weitere Bilder oder Reisebilder benutzen Sie bitte irgendwelche Bilder als Platzhalter.
Mit uns erleben Sie die schönsten Theater und Spielorte Europas, wie Sie sie noch nie erlebt haben!
Unsere exklusiven Bus-Touren richten sich an Menschen mit hohen Erwartungen, die es gewohnt sind auf Ihren Reisen auf nichts zu verzichten. Mit unseren 5 Sterne-Bussen bieten wir Ihnen einen der höchsten Standards der Reisebusbranche. Natürlich werden alle Reisen von einer Servicekraft begleitet, die nicht nur Ihr Ansprechpartner während der Fahrt ist, sondern sich auch mit einem Getränke- und Snack-Service um Ihr Wohl kümmert und sich im hinteren Bereich in der Kids Lounge um die kleineren Gäste kümmert. Spielen, Basteln .. für alles ist gesorgt. Ein bequemer Sitzabstand von 81cm lässt Ihnen viel Bewegungsfreiheit. Mit der verstellbaren Fußstütze können sie sich zurücklehnen und entspannen! Der Stromanschluss zum laden Ihres Smartphones oder Tablets ist natürlich Standard. Darüber hinaus sind unsere Busse mit kostenfreien WiFi-Hotspots ausgerüstet. Sie können also noch während Ihrer Reise Bilder an Ihre Freunde und Verwandte senden, Ihre Emails lesen oder z.B. Ihre Lieblingsmusik streamen.
Auch bei den Hotels machen wir keine Abstriche. Auf allen Mehrtagestouren, die Sie bei uns buchen, werden Sie in mindestens 4 Sterne-Hotels untergebracht. Bei der Auswahl der Unterkünfte achten wir natürlich darauf, dass diese der Reise angepasst sind. D.h. bei z.B. Städtereisen möglichst zentrumsnah und bei Konzertre..
Aufgabenstellung
32 Seiten, A4 Quadrat,
Datenformat (inkl. 2,00 mm Beschnitt): 21,40 x 21,40 cm
Endformat (offen): 42,00 x 21,00 cm
Endformat (geschlossen): 21,00 x 21,00 cm

```html
<!DOCTYPE html>
<html lang="de">
<head>
<meta charset="utf-8">
<title>Kai Brenner Reisen – Prospekt</title>
<link href="https://fonts.googleapis.com/css2?family=Roboto:ital,wght@0,400;0,500;0,700;0,900;1,400&display=swap" rel="stylesheet">
<style>
:root{
  --navy:#0c2677;
  --orange:#f2693a;
  --ink:#1c1c1c;
  --white:#ffffff;
  --rule:#6f86c8;
}
*{margin:0;padding:0;box-sizing:border-box}
html,body{width:1200px;height:2301px;overflow:hidden;background:#fff}
body{position:relative;font-family:'Roboto',sans-serif;color:var(--ink)}
.abs{position:absolute}
.photo{position:absolute}
/* cover */
.cover-strip{left:93px;top:77px;width:13px;height:505px;background:var(--navy)}
.cover-photo{left:106px;top:77px;width:492px;height:505px;background:linear-gradient(180deg,#cfe0e4 0%,#d8d2c2 35%,#b07a4b 60%,#5b4436 85%,#3a3330 100%)}
.cover-card{left:106px;top:77px;width:147px;height:233px;background:var(--white)}
.brand-name{left:120px;top:102px;font-size:9px;font-weight:700;letter-spacing:2.4px;color:var(--ink)}
.brand-sub{left:120px;top:118px;display:flex;align-items:center;gap:6px;font-size:8px;font-weight:700;color:var(--ink);letter-spacing:.5px}
.brand-sub i{width:9px;height:9px;background:var(--ink);border-radius:50%;display:block}
.cover-head{left:117px;top:210px;font-size:17.5px;line-height:18.5px;font-weight:500;color:var(--orange)}
.cover-sub{left:117px;top:268px;font-size:9px;line-height:10px;color:var(--navy)}
.contact{left:439px;top:497px;width:159px;height:49px;background:var(--navy);color:#fff;padding:11px 0 0 20px}
.contact b{display:block;font-size:13px;font-weight:700}
.contact span{display:block;font-size:7.5px;font-weight:500;margin-top:1px}
/* spread 2 */
.s2-photo{left:93px;top:623px;width:1010px;height:505px;background:linear-gradient(180deg,#5f7ea3 0%,#7e93ad 40%,#4a556a 65%,#2b2a2c 82%,#3a2f26 100%)}
.fold{position:absolute;width:1px;background:rgba(255,255,255,.35)}
.kicker{font-size:10.5px;font-weight:700;color:#fff;letter-spacing:.4px}
.kicker small{display:block;font-size:6.5px;font-weight:400;letter-spacing:0}
.welcome{left:124px;top:707px;font-size:31.5px;line-height:31px;font-weight:700;color:#fff}
.lead{left:124px;top:775px;width:420px;font-size:13.5px;line-height:16px;color:#fff}
.fine{font-size:7px;line-height:10px;color:#fff}
.list{font-size:8.5px;color:#fff}
.framed{border:2px solid #fff}
.pg{font-size:7px;color:#fff}
/* spread 3 */
.band{top:1179px;height:147px}
.sheet{left:93px;top:1326px;width:1010px;height:333px;background:#fff;border-left:1px solid #ddd;border-right:1px solid #ddd}
.tour{position:absolute;top:1340px;width:142px}
.tour h3{font-size:12px;line-height:14px;font-weight:700;height:30px}
.tour .t-label{font-size:7px;color:var(--orange);margin-top:0}
.tour .dates{font-size:7px;line-height:10px}
.tour hr{border:0;border-top:1px solid var(--rule);margin:7px 0 8px}
.tour .body{font-size:7.3px;line-height:10px;height:124px}
.tour .perf{font-size:7px;line-height:10px;font-style:italic;color:var(--navy);height:48px}
.price{display:flex;justify-content:space-between;font-size:7px;line-height:12px}
.price b{color:var(--orange);font-size:10.5px;font-weight:500}
.tour .note{font-size:7px;line-height:10px;font-style:italic;color:var(--navy);margin-top:4px}
.footbar{left:93px;top:1659px;width:1010px;height:25px;background:var(--navy)}
/* spread 4 */
.s4-bg{left:93px;top:1714px;width:687px;height:311px;background:linear-gradient(180deg,#e3c48c 0%,#f1e2c3 40%,#f8f2e6 100%)}
.s4-arch{left:598px;top:1714px;width:182px;height:311px;background:linear-gradient(180deg,#c9b089 0%,#e7dcc6 60%,#f5efe3 100%)}
.s4-right{left:780px;top:1714px;width:323px;height:506px;background:linear-gradient(180deg,#6a6a6a 0%,#8a8580 30%,#5a4630 60%,#2a2119 100%)}
.dresden{left:129px;top:1763px;font-size:30px;font-weight:900;color:#151515;letter-spacing:.3px}
.tag{left:270px;top:1742px;width:96px;height:38px;transform:rotate(-8deg)}
.tag-text{left:284px;top:1745px;font-size:22px;font-weight:700;color:#151515;transform:rotate(-8deg)}
.termbox{left:93px;top:1807px;width:189px;height:42px;background:var(--navy);color:#fff;font-size:7px;line-height:10px;padding:5px 0 0 36px}
.story{left:129px;top:1857px;width:214px;font-size:7.3px;line-height:10px}
.story .perf{font-style:italic;color:var(--navy);margin-top:4px}
.prog{left:356px;top:1857px;width:200px;font-size:7.3px;line-height:10px}
.prog ol{padding-left:10px;margin-top:5px}
.prog li{margin-bottom:4px}
.early{left:466px;top:1935px;font-size:7px;display:flex;gap:8px;align-items:center}
.early b{font-size:13px;font-weight:700}
.navybar{left:93px;top:2200px;width:687px;height:20px;background:var(--navy)}
</style>
</head>
<body>

<!-- Cover -->
<section class="cover">
  <div class="abs cover-photo" role="img" aria-label="Altstadtgasse mit Fachwerkhäusern und Torturm in der Abenddämmerung"></div>
  <div class="abs cover-strip"></div>
  <div class="abs cover-card"></div>
  <div class="abs brand-name">KAI BRENNER</div>
  <div class="abs brand-sub"><i></i>REISEN</div>
  <h1 class="abs cover-head">EINMALIG...<br>BESONDERS...<br>SORGENFREI...</h1>
  <p class="abs cover-sub">Urlaub von Anfang an<br>ohne Kompromisse…</p>
  <div class="abs contact"><b>+49 170 555 01 23</b><span>reise@brenner-reisen.de</span></div>
</section>

<!-- Welcome spread -->
<section class="welcome-spread">
  <div class="abs s2-photo" role="img" aria-label="Bergsee in der Dämmerung mit beleuchtetem Reisebus"></div>
  <div class="fold" style="left:598px;top:623px;height:505px"></div>
  <div class="abs kicker" style="left:124px;top:642px">MIT UNS ERLEBEN SIE<small>Mit uns erleben Sie</small></div>
  <h2 class="abs welcome">HERZLICH WILLKOMMEN<br>BEI KAI BRENNER!</h2>
  <p class="abs lead">Lorem Ipsum ist ein einfacher Demo-Text für die Print- und Schriftindustrie. Lorem Ipsum ist in der Industrie bereits der Standard Demo-Text seit 1500, als ein unbekannter Schriftsteller eine Hand voll Wörter nahm und diese</p>
  <p class="abs fine" style="left:124px;top:860px;width:212px">Lorem Ipsum ist ein einfacher Demo-Text für die Print- und Schriftindustrie. Lorem Ipsum ist in der Industrie bereits der Standard Demo-Text seit 1500, als ein unbekannter Schriftsteller eine Hand voll Wörter nahm und diese durcheinander warf um ein Musterbuch zu erstellen. Es hat nicht nur 5 Jahrhunderte überlebt, sondern auch in Spruch in die elektronische Schriftbearbeitung geschafft (bemerke, nahezu unverändert). Bekannt wurde es 1960, mit dem</p>
  <p class="abs fine" style="left:356px;top:860px;width:212px">Lorem Ipsum ist ein einfacher Demo-Text für die Print- und Schriftindustrie. Lorem Ipsum ist in der Industrie bereits der Standard Demo-Text seit 1500, als ein unbekannter Schriftsteller eine Hand voll Wörter nahm und diese durcheinander warf um ein Musterbuch zu erstellen. Es hat nicht nur 5 Jahrhunderte überlebt, sondern auch in Spruch in die elektronische Schriftbearbeitung geschafft (bemerke, nahezu unverändert). Bekannt wurde es 1960, mit dem</p>
  <div class="abs list" style="left:160px;top:983px">Lorem Ipsum ist ein</div>
  <div class="abs list" style="left:160px;top:1008px">Lorem Ipsum ist ein</div>
  <div class="abs list" style="left:160px;top:1033px">Lorem Ipsum ist ein</div>
  <div class="abs list" style="left:354px;top:983px">Lorem Ipsum ist ein</div>
  <div class="abs list" style="left:354px;top:1008px">Lorem Ipsum ist ein</div>
  <div class="abs list" style="left:354px;top:1033px">Lorem Ipsum ist ein</div>
  <div class="photo framed" style="left:497px;top:965px;width:208px;height:143px;background:linear-gradient(180deg,#9fb7c9,#b08a66 60%,#6b4a33)" role="img" aria-label="Innenraum des Reisebusses mit Ledersitzen"></div>
  <div class="photo" style="left:804px;top:623px;width:299px;height:177px;background:linear-gradient(180deg,#e8ebef,#c9ccd2 60%,#9a9ea6)" role="img" aria-label="Inhaber im Büro am Besprechungstisch"></div>
  <div class="photo framed" style="left:965px;top:817px;width:123px;height:162px;background:linear-gradient(180deg,#c8ccd0,#8b6d52 60%,#5b4433)" role="img" aria-label="Sitzreihen im Bus"></div>
  <p class="abs fine" style="left:641px;top:711px;width:145px">Lorem Ipsum ist ein einfacher Demo-Text für die Print- und Schriftindustrie. Lorem Ipsum ist in der Industrie bereits der Standard Demo-Text seit 1500, als ein unbekannter Schriftsteller eine Hand voll Wörter nahm und diese durcheinander warf um ein Musterbuch zu erstellen. Es hat nicht nur 5 Jahrhunderte überlebt, sondern auch in Spruch in die elektronische Schriftbearbeitung geschafft (bemerke, nahezu</p>
  <p class="abs" style="left:641px;top:836px;width:150px;font-size:13px;line-height:16px;color:#fff">Lorem Ipsum ist ein einfacher Demo-Text für die Print- und Schriftindustrie. Lorem</p>
  <p class="abs fine" style="left:641px;top:908px;width:145px;font-style:italic">Lorem Ipsum ist ein einfacher Demo-Text für die Print- und Schriftindustrie. Lorem Ipsum ist in der Industrie bereits der</p>
  <div class="abs pg" style="left:124px;top:1100px">2</div>
  <div class="abs pg" style="left:1067px;top:1100px">3</div>
</section>

<!-- Tours spread -->
<section class="tours">
  <div class="photo band" style="left:93px;width:505px;background:linear-gradient(180deg,#3b2f2a,#6b4a36 50%,#4a3a33)" role="img" aria-label="Burg im herbstlichen Wald"></div>
  <div class="photo band" style="left:598px;width:505px;background:linear-gradient(180deg,#1f2e47,#2c3d5a 50%,#1a2436)" role="img" aria-label="Stadtsilhouette bei Nacht am Fluss"></div>
  <div class="abs kicker" style="left:124px;top:1198px">MEHRTAGESREISEN</div>
  <div class="abs kicker" style="left:629px;top:1198px">TAGESTOUREN</div>
  <div class="abs sheet"></div>
  <div class="fold" style="left:598px;top:1326px;height:333px;background:#ddd"></div>

  <article class="tour" style="left:124px">
    <h3>Antwerpen, Brüssel, Gent und Brügge</h3>
    <div class="t-label">Termine:</div>
    <div class="dates"><b>09.04.-13.04.2020</b> (05 084 20 Ostern)<br><b>26.08.-30.08.2020</b> (05 085 20 Sommer)</div>
    <hr>
    <p class="body">Lassen Sie sich von der Vielfalt und dem Charme Flanderns verzaubern. Die Diamantenhauptstadt Antwerpen ist eine sehr bunte und lebendige Stadt mit einer blühenden Kunstszene. Gent und Brügge bezaubern mit engen Gassen, Kanälen und Brü- cken. Belgiens Hauptstadt Brüssel besticht mit ihren starken Kontrasten: klassische Jugendstil-architektur, historische Kirchen finden sich hier neben dem futuristischen Sitz der EU und trendige Szenecafés neben</p>
    <p class="perf">Leistungen: Busreise, 1 Übernachtung mit Früh- stücksbuffet im guten 3***-Stadthotel Dresden Neustadt, Reiseleitung</p>
    <div class="price"><span>Frühbucherpreis</span><b>€188</b></div>
    <div class="price"><span>Normalpreis</span><b>€208</b></div>
    <p class="note">Frühbucherpreis gültig für Buchungen bis 6 Wochen vor Reisebeginn.</p>
  </article>
  <article class="tour" style="left:273px">
    <h3>Faszinierendes Veneto 3 Tage - 3 Städte</h3>
    <div class="t-label">Termine:</div>
    <div class="dates"><b>09.04.-13.04.2020</b> (05 084 20 Ostern)<br><b>26.08.-30.08.2020</b> (05 085 20 Sommer)</div>
    <hr>
    <p class="body">Lassen Sie sich von der Vielfalt und dem Charme Flanderns verzaubern. Die Diamantenhauptstadt Antwerpen ist eine sehr bunte und lebendige Stadt mit einer blühenden Kunstszene. Gent und Brügge bezaubern mit engen Gassen, Kanälen und Brü- cken. Belgiens Hauptstadt Brüssel besticht mit ihren starken Kontrasten: klassische Jugendstilarchitek- tur, historische</p>
    <p class="perf">Leistungen: Busreise, 1 Übernachtung mit Früh- stücksbuffet im guten 3***-Stadthotel Dresden Neustadt, Reiseleitung</p>
    <div class="price"><span>Frühbucherpreis</span><b>€188</b></div>
    <div class="price"><span>Normalpreis</span><b>€208</b></div>
    <p class="note">Frühbucherpreis gültig für Buchungen bis 6 Wochen vor Reisebeginn.</p>
  </article>
  <article class="tour" style="left:423px">
    <h3>London</h3>
    <div class="t-label">Termine:</div>
    <div class="dates"><b>09.04.-13.04.2020</b> (05 084 20 Ostern)<br><b>26.08.-30.08.2020</b> (05 085 20 Sommer)</div>
    <hr>
    <p class="body">Lassen Sie sich von der Vielfalt und dem Charme Flanderns verzaubern. Die Diamantenhauptstadt Antwerpen ist eine sehr bunte und lebendige Stadt mit einer blühenden Kunstszene. Gent und Brügge bezaubern mit engen Gassen, Kanälen und Brü- cken. Belgiens Hauptstadt Brüssel besticht mit ihren starken Kontrasten: klassische Jugendstilarchitek- tur, historische Kirchen finden sich hier neben dem futuristischen Sitz der EU und trendige</p>
    <p class="perf">Leistungen: Busreise, 1 Übernachtung mit Früh- stücksbuffet im guten 3***-Stadthotel Dresden Neustadt, Reiseleitung</p>
    <div class="price"><span>Frühbucherpreis</span><b>€188</b></div>
    <div class="price"><span>Normalpreis</span><b>€208</b></div>
    <p class="note">Frühbucherpreis gültig für Buchungen bis 6 Wochen vor Reisebeginn.</p>
  </article>
  <article class="tour" style="left:629px">
    <h3>Amsterdam</h3>
    <div class="t-label">Termine:</div>
    <div class="dates"><b>09.04.-13.04.2020</b> (05 084 20 Ostern)<br><b>26.08.-30.08.2020</b> (05 085 20 Sommer)</div>
    <hr>
    <p class="body">Lassen Sie sich von der Vielfalt und dem Charme Flanderns verzaubern. Die Diamantenhauptstadt Antwerpen ist eine sehr bunte und lebendige Stadt mit einer blühenden Kunstszene. Gent und Brügge bezaubern mit engen Gassen, Kanälen und Brü- cken. Belgiens Hauptstadt Brüssel besticht mit ihren starken Kontrasten: klassische Jugendstil-architektur, historische Kirchen finden sich hier neben dem futuristischen Sitz der EU und trendige Szenecafés neben</p>
    <p class="perf">Leistungen: Busreise, 1 Übernachtung mit Früh- stücksbuffet im guten 3***-Stadthotel Dresden Neustadt, Reiseleitung</p>
    <div class="price"><span>Frühbucherpreis</span><b>€188</b></div>
    <div class="price"><span>Normalpreis</span><b>€208</b></div>
    <p class="note">Frühbucherpreis gültig für Buchungen bis 6 Wochen vor Reisebeginn.</p>
  </article>
  <article class="tour" style="left:778px">
    <h3>Karneval in Venedig</h3>
    <div class="t-label">Termine:</div>
    <div class="dates"><b>09.04.-13.04.2020</b> (05 084 20 Ostern)<br><b>26.08.-30.08.2020</b> (05 085 20 Sommer)</div>
    <hr>
    <p class="body">Lassen Sie sich von der Vielfalt und dem Charme Flanderns verzaubern. Die Diamantenhauptstadt Antwerpen ist eine sehr bunte und lebendige Stadt mit einer blühenden Kunstszene. Gent und Brügge bezaubern mit engen Gassen, Kanälen und Brü- cken. Belgiens Hauptstadt Brüssel besticht mit ihren starken Kontrasten: klassische</p>
    <p class="perf">Leistungen: Busreise, 1 Übernachtung mit Früh- stücksbuffet im guten 3***-Stadthotel Dresden Neustadt, Reiseleitung</p>
    <div class="price"><span>Frühbucherpreis</span><b>€188</b></div>
    <div class="price"><span>Normalpreis</span><b>€208</b></div>
    <p class="note">Frühbucherpreis gültig für Buchungen bis 6 Wochen vor Reisebeginn.</p>
  </article>
  <article class="tour" style="left:928px">
    <h3>Paris</h3>
    <div class="t-label">Termine:</div>
    <div class="dates"><b>09.04.-13.04.2020</b> (05 084 20 Ostern)<br><b>26.08.-30.08.2020</b> (05 085 20 Sommer)</div>
    <hr>
    <p class="body">Lassen Sie sich von der Vielfalt und dem Charme Flanderns verzaubern. Die Diamantenhauptstadt Antwerpen ist eine sehr bunte und lebendige Stadt mit einer blühenden Kunstszene. Gent und Brügge bezaubern mit engen Gassen, Kanälen und Brü- cken. Belgiens Hauptstadt Brüssel besticht mit ihren starken Kontrasten: klassische Jugendstilarchitek- tur, historische Kirchen finden sich hier neben dem futuristischen Sitz der EU und trendige</p>
    <p class="perf">Leistungen: Busreise, 1 Übernachtung mit Früh- stücksbuffet im guten 3***-Stadthotel Dresden Neustadt, Reiseleitung</p>
    <div class="price"><span>Frühbucherpreis</span><b>€188</b></div>
    <div class="price"><span>Normalpreis</span><b>€208</b></div>
    <p class="note">Frühbucherpreis gültig für Buchungen bis 6 Wochen vor Reisebeginn.</p>
  </article>
  <div class="abs footbar"></div>
  <div class="abs pg" style="left:124px;top:1667px">4</div>
  <div class="abs pg" style="left:1067px;top:1667px">5</div>
</section>

<!-- Dresden spread -->
<section class="destination">
  <div class="abs s4-bg" role="img" aria-label="Heller Säulengang mit Bögen"></div>
  <div class="abs s4-arch" role="img" aria-label="Säulen und Innenhof eines Palastes"></div>
  <div class="abs s4-right" role="img" aria-label="Kuppelkirche unter dramatischem Himmel"></div>
  <div class="fold" style="left:598px;top:1714px;height:311px"></div>
  <h2 class="abs dresden">DRESDEN</h2>
  <svg class="abs tag" viewBox="0 0 96 38" aria-hidden="true"><rect x="2" y="2" width="92" height="34" fill="none" stroke="var(--orange)" stroke-width="3"/></svg>
  <div class="abs tag-text">€208</div>
  <div class="abs termbox"><b>Termine:</b><br><b>09.04.-13.04.2020</b> (05 084 20 Ostern)<br><b>26.08.-30.08.2020</b> (05 085 20 Sommer)</div>
  <div class="abs story">
    <p>Reich an Kunst und Kultur zeigt sich Sachsens Landeshauptstadt vor barocker Ku- lisse. Voller Le- bensfreude genießen die Dresdener ihre Stadt auf Straßen und Plätzen, auf Bühnen mit Künstlern von Weltrang und laden Gäste aus aller Welt ein, es ihnen gleich zu tun. Auch die Zahl der Sehenswür- digkeiten ist groß. Die Frauenkirche, das Schloß, die Semperoper, das grüne Gewölbe und viele weitere Attraktionen warten darauf, von Ihnen entdeckt zu werden.</p>
    <p class="perf"><b>Leistungen:</b> Busreise, 1 Übernachtung mit Früh- stücksbuffet im guten 3***-Stadthotel Dresden Neustadt, Reiseleitung</p>
    <p class="perf">Frühbucherpreis gültig für Buchungen bis 6 Wochen vor Reisebeginn.</p>
  </div>
  <div class="abs prog">
    <b>Programm:</b>
    <ol>
      <li>Tag: Abfahrt 06.00 Uhr Augsburg, Plärrer, nach Ankunft in Dresden Freizeit, 18.00 Uhr Hotelbezug</li>
      <li>Tag: vormittags Stadtführung (€ 18,–), Zeit zur freien Verfügung,</li>
      <li>15.00 Uhr Rückfahrt, Ankunft abends</li>
    </ol>
  </div>
  <div class="abs early"><span>Frühbucherpreis</span><b>€188</b></div>
  <div class="photo" style="left:93px;top:2025px;width:202px;height:175px;background:linear-gradient(180deg,#e6e2d8,#c9b68a 60%,#9c8a64)" role="img" aria-label="Kircheninnenraum mit Orgel"></div>
  <div class="photo" style="left:297px;top:2025px;width:200px;height:175px;background:linear-gradient(180deg,#3a3632,#5d4a3a 50%,#2c2724)" role="img" aria-label="Besucher vor einem Gemälde in der Galerie"></div>
  <div class="photo" style="left:498px;top:2025px;width:282px;height:175px;background:linear-gradient(90deg,#6a4a2c,#8c6a44 50%,#2a3f66)" role="img" aria-label="Altstadtplatz bei Nacht"></div>
  <div class="abs navybar"></div>
  <div class="abs pg" style="left:124px;top:2206px">4</div>
  <div class="abs pg" style="left:1067px;top:2206px">5</div>
</section>

</body>
</html>
```